Business Card Design Project

We are rebranding an existing automotive collision repair business. The business is called dent haven. I have attached logo but I'm not tied to that. I want to leave this wide open.

I want this card to say we are professional, competent, cutting edge. We are focused on customers and use a lot of the latest technology to make the customer experience different. We sign customers in on iPads. Paperwork I signed electronically and updates are sent via text, email, logging on a website or as they wish. I want this innovation and image to come through in our cards

Target Market(s)

60%. Women 40% men. Age 35-60

Industry/Entity Type

Automotive

Requirements
Must have
• The card must have name, title, phone,email, cell, web page

```html
<!DOCTYPE html>
<html lang="en">
<head>
<meta charset="utf-8">
<title>Dent Haven – Business Card</title>
<link href="https://fonts.googleapis.com/css2?family=Arimo:wght@400;700&display=swap" rel="stylesheet">
<style>
  :root {
    --green: #66bb46;
    --green-soft: #d9eed0;
    --grey: #c8c8ca;
    --grey-band: #c4c4c6;
    --white: #ffffff;
    --page: #ffffff;
    --rule: rgba(255,255,255,0.85);
  }
  * { box-sizing: border-box; margin: 0; padding: 0; }
  html, body {
    width: 1200px; height: 800px; overflow: hidden;
    background: var(--page);
    font-family: "Arimo", Arial, sans-serif;
  }
  .sheet {
    position: absolute; left: 306px; top: 42px;
    width: 437px; height: 534px;
    transform: scale(1.35); transform-origin: 0 0;
  }
  .card {
    position: absolute; left: 0;
    width: 437px; height: 249px;
    box-shadow: 0 12px 10px -8px rgba(0,0,0,0.28);
  }
  .card--front { top: 0; background: var(--white); border: 1px solid #ececec; }
  .card--back { top: 285px; background: var(--grey); }

  /* brand lockup */
  .brand {
    position: absolute; display: flex; align-items: center; gap: 6px;
    font-weight: 700; font-size: 11px; letter-spacing: 0.3px;
  }
  .brand__dot { width: 12px; height: 12px; border-radius: 50%; }
  .card--front .brand { left: 25px; top: 54px; color: var(--green); }
  .card--front .brand__dot { background: var(--green); }
  .card--back .brand { right: 24px; top: 57px; color: var(--white); }
  .card--back .brand__dot { background: var(--white); }

  /* front */
  .name-band {
    position: absolute; left: 0; top: 125px; width: 165px; height: 48px;
    background: var(--grey-band); color: var(--white);
    font-weight: 700; font-size: 14.5px;
    display: flex; align-items: center; justify-content: center;
  }
  .contact-table {
    position: absolute; left: 170px; top: 125px; width: 265px;
    background: var(--green); color: var(--white);
  }
  .row { display: flex; height: 29px; border-top: 1px solid var(--rule); align-items: center; }
  .row:first-child { border-top: none; }
  .row__key {
    width: 17px; height: 100%; font-weight: 700; font-size: 12.5px;
    display: flex; align-items: center; justify-content: center;
    border-right: 1px solid var(--rule);
  }
  .row__value { padding-left: 6px; font-size: 12.5px; height: 100%; display: flex; align-items: center; }
  .row__value + .row__key { border-left: 1px solid var(--rule); }
  .person { font-size: 16.5px; padding-left: 3px; }
  .person__name { font-weight: 700; }
  .contact-table .row:nth-child(2) .row__value { width: 108px; }

  /* back */
  .address-table {
    position: absolute; left: 0; top: 125px; width: 266px;
    background: var(--green); color: var(--green-soft);
  }
  .address-table .row__key { color: var(--white); width: 20px; border-right: none; align-items: flex-start; padding-top: 6px; }
  .address-table .row--address { height: 59px; }
  .address-table .row--web .row__key { align-items: center; padding-top: 0; }
  .address-lines { padding: 5px 0 0 12px; font-size: 12.5px; line-height: 16px; }
  .address-table .row__value { padding-left: 14px; }
  .tag-band {
    position: absolute; left: 270px; top: 125px; width: 167px; height: 48px;
    background: var(--white); color: var(--green);
    font-weight: 700; font-size: 14.5px;
    display: flex; align-items: center; justify-content: center;
  }
</style>
</head>
<body>
  <main class="sheet">
    <section class="card card--front" aria-label="Card front">
      <div class="brand"><span class="brand__dot"></span>DENT HAVEN</div>
      <div class="name-band">DENT HAVEN</div>
      <div class="contact-table">
        <div class="row"><span class="person"><span class="person__name">Maren Cole</span> - Director</span></div>
        <div class="row">
          <span class="row__key">M</span><span class="row__value">+1(800)555-0142</span>
          <span class="row__key">M</span><span class="row__value">+1(800)555-0142</span>
        </div>
        <div class="row"><span class="row__key">E</span><span class="row__value">hello@denthaven.com</span></div>
      </div>
    </section>

    <section class="card card--back" aria-label="Card back">
      <div class="brand"><span class="brand__dot"></span>DENT HAVEN</div>
      <div class="address-table">
        <div class="row row--address">
          <span class="row__key">A</span>
          <div class="address-lines">Dummy dummy dummy<br>dummy dummyDummy Street<br>dummy dummy XYZ City</div>
        </div>
        <div class="row row--web"><span class="row__key">W</span><span class="row__value">www.denthaven.com</span></div>
      </div>
      <div class="tag-band">DENT HAVEN</div>
    </section>
  </main>
</body>
</html>
```